Quorva - corporate Business Card

We need a good look and innovative business card for a new start up company based in Los Angeles called "Quorva". We are in a payment business, including payment card, app, and ewallet. We are expert in online payment and Card not present (CNP) transaction.
We need an innovative, modern business card.

Our logo font is Aero Matics

Target Market(s)

Startup - Bank - Online Payment - Card Manufacturing

Industry/Entity Type

Startup

Contact Information for Business Card

phone: 555 014 7396 - Address: 4172 Marlowe blvd, Vellmont, CA 90299

Requirements
Must have
• Message: innovative, professional, expert, high tech, trust, online payment expert, security
Nice to have
• no comment
Should not have
• no Comment

```html
<!DOCTYPE html>
<html lang="en">
<head>
<meta charset="utf-8">
<title>Quorva — Business Card</title>
<link rel="stylesheet" href="https://fonts.googleapis.com/css2?family=Montserrat:wght@400;500;600&display=swap">
<style>
  :root {
    --brand-red: #b81c2e;
    --paper: #ffffff;
    --ink-grey: #6a6a6a;
    --backdrop: #2b2b2d;
  }
  * { box-sizing: border-box; margin: 0; padding: 0; }
  html, body {
    width: 1200px; height: 950px; overflow: hidden;
    background: var(--backdrop);
    font-family: "Montserrat", sans-serif;
  }
  .sheet { position: relative; width: 1200px; height: 950px; }

  .card {
    position: absolute; top: 125px;
    width: 400px; height: 700px;
    background: var(--brand-red);
    overflow: hidden;
    border-radius: 3px;
  }
  .card--front { left: 160px; }
  .card--back  { left: 640px; }

  .card__arch { position: absolute; inset: 0; width: 400px; height: 700px; }

  .card__title {
    position: absolute; top: 30px; right: 34px;
    color: var(--paper);
    font-size: 17px; font-weight: 600; letter-spacing: 0.5px;
  }
  .card__title .role { font-weight: 400; }

  /* rotated content: reads bottom-to-top along the long edge */
  .vertical {
    position: absolute;
    transform: rotate(-90deg);
    transform-origin: left top;
  }
  .front-info { left: 48px; top: 660px; width: 460px; height: 320px; }
  .back-info  { left: 70px; top: 650px; width: 560px; height: 300px; }

  .brand { display: flex; align-items: center; gap: 14px; }
  .brand__dot { width: 74px; height: 74px; border-radius: 50%; flex: none; }
  .brand__name { font-size: 72px; font-weight: 500; line-height: 1; letter-spacing: -1px; }

  .brand--front .brand__dot { background: var(--brand-red); }
  .brand--front .brand__name { color: var(--brand-red); }

  .brand--back .brand__dot { width: 110px; height: 110px; background: var(--paper); }
  .brand--back .brand__name { color: var(--paper); font-size: 104px; }

  .contact {
    margin-top: 22px;
    color: var(--ink-grey);
    font-size: 15px; line-height: 22px;
    list-style: none;
  }
  .contact li { display: flex; align-items: center; gap: 8px; }
  .contact svg { width: 14px; height: 14px; flex: none; fill: var(--brand-red); }
  .contact .address { margin-bottom: 4px; }

  .website {
    color: var(--paper);
    font-size: 13px; letter-spacing: 6px;
    margin-bottom: 36px; padding-left: 4px;
  }
</style>
</head>
<body>
<main class="sheet">

  <section class="card card--front" aria-label="Card front">
    <svg class="card__arch" viewBox="0 0 400 700" aria-hidden="true">
      <path d="M0 700 V250 A230 230 0 0 1 400 380 V700 Z" fill="var(--paper)"/>
    </svg>
    <p class="card__title">MARA VOSS - <span class="role">PRESIDENT</span></p>

    <div class="vertical front-info">
      <div class="brand brand--front">
        <span class="brand__dot"></span>
        <span class="brand__name">Quorva</span>
      </div>
      <ul class="contact">
        <li class="address">4172 Marlowe blvd<br>Vellmont, CA 90299</li>
        <li>
          <svg viewBox="0 0 16 16"><path d="M3 1h3l1.5 4-2 1.2a9 9 0 0 0 4.3 4.3L11 8.5l4 1.5v3a2 2 0 0 1-2 2A12 12 0 0 1 1 3a2 2 0 0 1 2-2z"/></svg>
          555 014 7396
        </li>
        <li>
          <svg viewBox="0 0 16 16"><path d="M1 3h14v10H1z M1 3l7 6 7-6" fill="var(--brand-red)" stroke="#fff" stroke-width="1.2"/></svg>
          mara@quorva.com
        </li>
        <li>
          <svg viewBox="0 0 16 16"><circle cx="8" cy="8" r="7"/><path d="M1 8h14M8 1c3 3 3 11 0 14M8 1c-3 3-3 11 0 14" stroke="#fff" stroke-width="1" fill="none"/></svg>
          www.quorva.com
        </li>
      </ul>
    </div>
  </section>

  <section class="card card--back" aria-label="Card back">
    <div class="vertical back-info">
      <p class="website">www.quorva.com</p>
      <div class="brand brand--back">
        <span class="brand__dot"></span>
        <span class="brand__name">Quorva</span>
      </div>
    </div>
  </section>

</main>
</body>
</html>
```